Quillbrookes websites redesign

Www.quill-brookes.com needs to be redesigned along with updations. The incremental material will be provided for the updations. We are looking for complete redesign of the pages with the new content. The complete write up will be provided soon

Target Market(s)

Global

Coding

Coded - Design and coding required

Number of Pages Required

5+ page

Requirements
Must have
• A clean and slick design for the Consulting.
Should not have
• Too many pictures which reduces the speed of the site

```html
<!DOCTYPE html>
<html lang="en">
<head>
<meta charset="utf-8">
<title>Quillbrookes Consultancy</title>
<link href="https://fonts.googleapis.com/css2?family=Exo+2:wght@300;400;600;700&display=swap" rel="stylesheet">
<style>
:root{
  --blue:#43a5d5;
  --blue-text:#3f9fcf;
  --navy:#243350;
  --navy-deep:#1c293f;
  --navy-field:#33476a;
  --ink:#2a3550;
  --body:#666b74;
  --pale:#f5f5f5;
  --white:#ffffff;
  --logo:#5a2a2a;
}
*{margin:0;padding:0;box-sizing:border-box}
html,body{width:762px;height:1200px;overflow:hidden;background:var(--white)}
body{font-family:"Exo 2",sans-serif;position:relative;color:var(--body)}
.abs{position:absolute}
.top-rule{left:0;top:0;width:762px;height:3px;background:var(--blue)}
.brand{left:62px;top:20px;display:flex;align-items:center;gap:7px;font-size:19px;font-weight:400;color:var(--logo)}
.brand-dot{width:20px;height:20px;border-radius:50%;background:var(--blue)}
.contact{left:534px;top:24px;display:flex;align-items:center;gap:9px;font-size:10px;color:#555;letter-spacing:.1px}
.hero{left:0;top:80px;width:762px;height:285px;background:linear-gradient(160deg,#5f6c7a 0%,#3e4a58 40%,#6d7885 75%,#9aa3ad 100%)}
.nav{left:62px;top:60px;width:636px;height:43px;background:var(--navy);display:flex;z-index:2}
.nav a{color:var(--white);font-size:9.5px;text-decoration:none;display:flex;align-items:center;justify-content:center;height:100%}
.nav a.active{background:var(--blue)}
.hero-title{left:0;width:762px;top:254px;text-align:center;color:var(--white);font-size:27px;font-weight:700}
.hero-sub{left:0;width:762px;top:289px;text-align:center;color:var(--white);font-size:16px;font-weight:600}
.arrow{top:210px}
.about{left:0;top:365px;width:762px;height:181px;background:var(--blue);text-align:center;color:var(--white)}
.sec-title{font-size:17px;font-weight:300;letter-spacing:-.2px}
.sec-title b{font-weight:700}
.about .sec-title{margin-top:30px;font-size:17px}
.about p{font-size:7.2px;line-height:13px;width:510px;margin:11px auto 0}
.btn{display:inline-flex;align-items:center;justify-content:center;font-size:10px;border:1.5px solid}
.about .btn{width:87px;height:29px;margin-top:16px;color:var(--white);border-color:var(--white)}
.founder{left:0;top:546px;width:762px;height:247px;background:var(--pale)}
.founder .sec-title{position:absolute;left:62px;top:27px;color:var(--ink);font-size:17px}
.founder-text{left:63px;top:60px;width:318px;font-size:7.2px;line-height:13px;color:var(--body)}
.founder-text p+p{margin-top:12px}
.founder .btn{position:absolute;left:64px;top:186px;width:87px;height:29px;color:var(--ink);border-color:var(--ink)}
.founder-photo{left:406px;top:576px;width:293px;height:187px;background:var(--white);padding:3px;box-shadow:0 0 2px rgba(0,0,0,.2)}
.founder-photo div{width:100%;height:100%;background:linear-gradient(135deg,#3b4a8a 0%,#2e3c78 55%,#5b4a6a 100%)}
.cases{left:0;top:793px;width:762px;text-align:center}
.cases .sec-title{margin-top:21px;color:var(--ink)}
.cases .lead{font-size:7.2px;margin-top:6px;color:var(--body)}
.case{top:878px;width:180px;text-align:center;color:var(--blue-text);font-size:10px;line-height:16.5px}
.case svg{display:block;margin:0 auto 12px}
.news{left:0;top:985px;width:762px;height:161px;background:var(--navy);text-align:center;color:var(--white)}
.news .sec-title{margin-top:24px}
.news p{font-size:7.2px;line-height:13px;width:480px;margin:8px auto 0}
.news-form{left:197px;top:1085px;display:flex}
.news-form span{width:218px;height:32px;background:var(--navy-field);color:#7f8ea8;font-size:8.5px;display:flex;align-items:center;padding-left:15px}
.news-form b{width:119px;height:32px;background:var(--blue);color:var(--white);font-weight:400;font-size:11px;display:flex;align-items:center;justify-content:center}
.footer{left:0;top:1146px;width:762px;height:54px;background:var(--navy-deep)}
.copy{left:62px;top:1166px;font-size:9px;color:var(--white)}
.social{left:575px;top:1160px;display:flex;gap:8px}
.social i{width:24px;height:24px;border:2px solid var(--white);border-radius:50%}
</style>
</head>
<body>
<div class="abs top-rule"></div>
<div class="abs brand"><span class="brand-dot"></span>Quillbrookes</div>
<div class="abs contact">
  <svg width="14" height="14" viewBox="0 0 14 14"><rect width="14" height="14" rx="2" fill="#43a5d5"/><path d="M4 3.5c.6-.4 1.1-.2 1.4.4l.6 1.2c.2.4 0 .8-.3 1l-.4.3c.4.9 1.1 1.6 2 2l.3-.4c.3-.3.7-.4 1-.2l1.2.6c.6.3.7.9.3 1.4-.8 1-2.1 1-3.4.1C5.4 8.8 4.6 7.8 4 6.6 3.3 5.3 3.3 4.2 4 3.5z" fill="#fff"/></svg>
  CONTACT US : (088)5550142876
</div>

<div class="abs hero" role="img" aria-label="Photo of a business meeting table with papers, a pen and a glass of water"></div>
<nav class="abs nav">
  <a class="active" style="width:112px">HOME</a>
  <a style="width:88px">FOUNDER</a>
  <a style="width:122px">CONSULTANCY</a>
  <a style="width:85px">SYSTEM</a>
  <a style="width:122px">CASE STUDIES</a>
  <a style="width:107px">CONTACT</a>
</nav>
<div class="abs hero-title">QUILLBROOKES</div>
<div class="abs hero-sub">Quillbrookes Consultancy Limited capitalizes</div>
<svg class="abs arrow" style="left:27px" width="10" height="14" viewBox="0 0 10 14"><path d="M7 2 2 7l5 5" fill="none" stroke="#fff" stroke-width="1.6"/></svg>
<svg class="abs arrow" style="left:725px" width="10" height="14" viewBox="0 0 10 14"><path d="M3 2l5 5-5 5" fill="none" stroke="#fff" stroke-width="1.6"/></svg>

<section class="abs about">
  <h2 class="sec-title">ABOUT <b>US</b></h2>
  <p>Quillbrookes Consultancy Limited capitalizes on synergies arising from trade and investment linkages between countries and knowledge of traditional and non-traditional pools of liquidity to provide consultancy services to Emerging country banks, Corporates and SMEs.The Consultancy provides bank neutral views to Corporates and SMEs in Asian emerging markets and helps in improving financial structure and efficient use of funds.</p>
  <span class="btn">Read More</span>
</section>

<section class="abs founder">
  <h2 class="sec-title">FOUNDER <b>RAVINA DESAI</b></h2>
  <div class="abs founder-text" style="top:60px">
    <p>Ms. Ravina Desai is the founder director of Quillbrookes Consultancy Limited (QCL) based at Hong Kong. Ravina worked as the Alternate Chief Executive of Harbourline Bank, Hong Kong Branch until Jan 2013, heading Corporate Banking business in North Asia and Export Credit Agency business globally. During her tenure, both the businesses increased multifold.</p>
    <p>Ravina started her banking career with Harbourline Bank Ltd, India's second largest bank in the year 2002 and in the next 10 years handled multiple leadership responsibilities in the Corporate, Institutional and International Banking space across India, North Asia, Americas and Europe.</p>
  </div>
  <span class="btn">Read More</span>
</section>
<div class="abs founder-photo"><div role="img" aria-label="Photo of the founder speaking at a podium at a business forum, with flowers and a banner behind"></div></div>

<section class="abs cases">
  <h2 class="sec-title">OUR <b>CASE STUDIES</b></h2>
  <p class="lead">Some of the deals completed by QCL are summarised below to describe the range of activities undertaken with Corporates</p>
</section>
<div class="abs case" style="left:63px">
  <svg width="42" height="42" viewBox="0 0 42 42" fill="none" stroke="#43a5d5" stroke-width="4"><circle cx="26" cy="15" r="7"/><circle cx="26" cy="15" r="12" stroke-dasharray="4 3.5"/><circle cx="10" cy="33" r="4" stroke-width="3"/><circle cx="10" cy="33" r="7" stroke-dasharray="3 2.5" stroke-width="3"/><circle cx="26" cy="36" r="3" stroke-width="2.5"/></svg>
  Export Credit Agency backed<br>long term Project financing
</div>
<div class="abs case" style="left:245px;width:180px">
  <svg width="42" height="42" viewBox="0 0 42 42"><path d="M4 2h18l8 8v10H4z" fill="#43a5d5"/><path d="M4 20h16v20H4z" fill="#43a5d5"/><path d="M9 14h16M9 19h14M9 24h10M9 29h8" stroke="#fff" stroke-width="2"/><circle cx="28" cy="28" r="7" fill="#fff" stroke="#43a5d5" stroke-width="3.5"/><path d="M33 33l6 6" stroke="#43a5d5" stroke-width="4"/></svg>
  Introducing Regional/Local banks for<br>International Subsidiary Banking
</div>
<div class="abs case" style="left:413px;width:180px">
  <svg width="42" height="42" viewBox="0 0 42 42" fill="none" stroke="#43a5d5" stroke-width="3.5"><path d="M3 1v38h39"/><path d="M9 32l9-10 6 5 12-15"/><path d="M30 10h8v8" /></svg>
  Structured Financing
</div>
<div class="abs case" style="left:544px;width:180px">
  <svg width="42" height="42" viewBox="0 0 42 42" fill="none" stroke="#43a5d5" stroke-width="2.5"><path d="M21 9a11 11 0 0 0-7 19v5h14v-5a11 11 0 0 0-7-19z"/><path d="M16 37h10"/><path d="M21 1v4M7 6l3 3M35 6l-3 3M2 19h4M36 19h4"/><path d="M21 14v9" stroke-width="3"/><circle cx="21" cy="27" r="1.3" fill="#43a5d5"/></svg>
  Bank Lines Business
</div>

<section class="abs news">
  <h2 class="sec-title">NEWSLETTER <b>SIGNUP</b></h2>
  <p>Quillbrookes Consultancy Limited capitalizes on synergies arising from trade and investment linkages between countries and knowledge of traditional and non-traditional pools of liquidity to provide consultancy services to Emerging country banks, Corporates and SMEs</p>
</section>
<div class="abs news-form"><span>Enter The Mail Id</span><b>Subscribe Now</b></div>

<footer class="abs footer"></footer>
<div class="abs copy">Copyrights@2016Companyname . all rights reserved</div>
<div class="abs social"><i></i><i></i><i></i><i></i></div>
</body>
</html>
```